Corporate Business Card

Very professional, Modern, Not to busy, include phone address email, website
(253) 617-4930, 18761 52nd Avenue S, Kent, WA 98047, martin@plumlinegroup.com, varkoworks.com

Target Market(s)

Manufacturing

Industry/Entity Type

Aero, machining, manufacturing, Off road racing

Contact Information for Business Card

Phone, address email, website

```html
<!DOCTYPE html>
<html lang="en">
<head>
<meta charset="utf-8">
<title>Varko Works – Business Card</title>
<link rel="stylesheet" href="https://fonts.googleapis.com/css2?family=Lato:wght@400;700;900&family=Russo+One&display=swap">
<style>
  :root {
    --navy: #173670;
    --red: #d7222c;
    --white: #ffffff;
    --ink: #4a4a4f;
    --backdrop: #2a2a2e;
  }
  * { margin: 0; padding: 0; box-sizing: border-box; }
  html, body { width: 1200px; height: 718px; overflow: hidden; }
  body {
    background: var(--backdrop);
    font-family: "Lato", sans-serif;
    position: relative;
  }
  .card {
    position: absolute;
    top: 210px;
    width: 520px;
    height: 297px;
    overflow: hidden;
    box-shadow: 0 10px 30px rgba(0,0,0,.45);
  }
  .card--front { left: 50px; background: var(--white); }
  .card--back { left: 630px; background: var(--navy); }
  .band { position: absolute; left: 0; width: 520px; display: block; }
  .band--top { top: 0; }
  .band--bottom { bottom: 0; }

  .brand {
    position: absolute;
    font-family: "Lato", sans-serif;
    font-weight: 900;
    text-transform: uppercase;
    letter-spacing: 1px;
    line-height: 1;
  }
  .card--front .brand {
    left: 44px; top: 62px;
    font-size: 34px;
    color: var(--navy);
  }
  .card--back .brand {
    left: 0; right: 0; top: 118px;
    text-align: center;
    font-size: 52px;
    color: var(--white);
  }

  .holder {
    position: absolute;
    right: 30px; top: 116px;
    text-align: right;
  }
  .holder__name {
    font-family: "Russo One", sans-serif;
    font-size: 21px;
    color: var(--red);
    letter-spacing: .5px;
    line-height: 1;
  }
  .holder__title {
    font-size: 13px;
    color: var(--navy);
    margin-top: 3px;
  }
  .contact {
    position: absolute;
    right: 30px; top: 170px;
    list-style: none;
    text-align: right;
    font-size: 11.5px;
    color: var(--ink);
    line-height: 1.45;
  }
  .contact li { display: flex; justify-content: flex-end; align-items: flex-start; gap: 8px; }
  .contact li + li { margin-top: 2px; }
  .contact svg { width: 10px; height: 10px; margin-top: 3px; flex: none; fill: var(--navy); }
</style>
</head>
<body>

<section class="card card--front" aria-label="Business card front">
  <svg class="band band--top" viewBox="0 0 520 20" height="20" aria-hidden="true">
    <polygon points="0,6 225,0 212,12 0,20" fill="var(--red)"/>
  </svg>
  <svg class="band band--bottom" viewBox="0 0 520 24" height="24" aria-hidden="true">
    <polygon points="228,24 244,12 520,0 520,24" fill="var(--navy)"/>
  </svg>

  <div class="brand">Varko Works</div>

  <div class="holder">
    <div class="holder__name">DANIEL KESSLER</div>
    <div class="holder__title">Managing Director</div>
  </div>

  <ul class="contact">
    <li><span>18761 52nd Avenue S<br>Kent, WA 98047</span>
      <svg viewBox="0 0 10 10"><path d="M5 0a3.5 3.5 0 0 0-3.5 3.5C1.5 6 5 10 5 10s3.5-4 3.5-6.5A3.5 3.5 0 0 0 5 0zm0 5a1.5 1.5 0 1 1 0-3 1.5 1.5 0 0 1 0 3z"/></svg></li>
    <li><span>(253) 617-4930</span>
      <svg viewBox="0 0 10 10"><path d="M2 0l2 2.5-1 1.2a6 6 0 0 0 3.3 3.3l1.2-1L10 8l-1.3 1.6C4.5 10 0 5.5.4 1.3z"/></svg></li>
    <li><span>martin@plumlinegroup.com</span>
      <svg viewBox="0 0 10 10"><path d="M0 2h10v6H0z M0 2l5 3.5L10 2" fill="var(--navy)" stroke="var(--white)" stroke-width=".8"/></svg></li>
    <li><span>www.varkoworks.com</span>
      <svg viewBox="0 0 10 10"><circle cx="5" cy="5" r="4.3" fill="none" stroke="var(--navy)" stroke-width="1.2"/><path d="M1 5h8M5 .7c-2 2.5-2 6.1 0 8.6M5 .7c2 2.5 2 6.1 0 8.6" fill="none" stroke="var(--navy)" stroke-width=".8"/></svg></li>
  </ul>
</section>

<section class="card card--back" aria-label="Business card back">
  <svg class="band band--top" viewBox="0 0 520 16" height="16" aria-hidden="true">
    <polygon points="185,0 520,0 520,4 198,16" fill="var(--white)"/>
  </svg>
  <svg class="band band--bottom" viewBox="0 0 520 22" height="22" aria-hidden="true">
    <polygon points="0,11 205,0 220,6 0,22" fill="var(--red)"/>
  </svg>

  <div class="brand">Varko Works</div>
</section>

</body>
</html>
```